International service dog training school needs web design

We need to upgrade our website. The website is https://brightmeadow.studio/
We help trainers and service dog programs learn how to train service dogs with the latest and most ethical training methods. We offer online and in-person coaching services. We would like to see designs that are engaging and communicate professionalism, expertise, and care for the dogs and people we work with. Please also keep the colors already in the logo in the design.

```html
<!DOCTYPE html>
<html lang="en">
<head>
<meta charset="utf-8">
<title>Bright Meadow Center for Medical Assistance Canines</title>
<link rel="stylesheet" href="https://fonts.googleapis.com/css2?family=Montserrat:wght@400;500;600;700&family=Varela+Round&display=swap">
<style>
:root{
  --teal:#0aa39a;
  --blue:#1f6fc3;
  --ink:#222222;
  --muted:#7b7b7b;
  --soft:#f4f4f4;
  --dark:#2c2c2c;
  --white:#ffffff;
}
*{box-sizing:border-box;margin:0;padding:0}
html,body{width:1200px;height:4428px;overflow:hidden}
body{position:relative;background:var(--white);font-family:"Montserrat",sans-serif;color:var(--ink)}
.abs{position:absolute}
a{color:inherit;text-decoration:none}

/* top bar */
.topbar{left:0;top:0;width:1200px;height:46px;background:var(--teal)}
.topbar-blue{left:880px;top:0;width:320px;height:46px;background:var(--blue)}
.topbar-info{left:112px;top:0;height:46px;display:flex;align-items:center;gap:12px;color:var(--white);font-size:13px;font-weight:500}
.topbar-info svg{width:12px;height:12px;fill:var(--white);margin-right:6px;vertical-align:-1px}
.social{width:34px;height:34px;border:1.5px solid var(--white);border-radius:50%}

/* nav */
.nav{left:0;top:46px;width:1200px;height:73px;background:var(--white);box-shadow:0 1px 4px rgba(0,0,0,.08);z-index:3}
.brand{display:flex;align-items:center;gap:10px;font-family:"Montserrat",sans-serif;font-weight:600;font-size:19px;color:var(--blue)}
.brand-dot{width:38px;height:38px;border:2px solid var(--blue);border-radius:50%}
.nav .brand{left:112px;top:17px}
.menu{left:373px;top:0;height:73px;display:flex;align-items:center;gap:22px;font-size:14px;font-weight:700;color:var(--ink)}
.menu span.caret::after{content:"";display:inline-block;width:5px;height:5px;border-right:1.5px solid var(--ink);border-bottom:1.5px solid var(--ink);transform:rotate(45deg);margin-left:8px;vertical-align:3px}

/* hero */
.hero-photo{left:0;top:119px;width:1200px;height:780px;background:linear-gradient(120deg,#4f7a2c 0%,#7fa24a 35%,#c7c3b0 55%,#6b9a3a 75%,#3f6d25 100%)}
.hero-title{left:112px;top:300px;font-size:29px;line-height:41px;font-weight:700;color:var(--white);letter-spacing:.3px}
.pill{display:flex;align-items:center;justify-content:center;border-radius:26px;color:var(--white);font-size:13.5px;font-weight:700}
.pill.teal{background:var(--teal)}
.pill.blue{background:var(--blue)}
.pill.white{background:var(--white);color:var(--teal)}
.hero-wave{left:0;top:600px;width:1200px;height:300px}

/* about */
.about-ring{left:112px;top:856px;width:456px;height:448px;border-radius:50%;border-left:7px solid var(--blue);border-bottom:3px solid var(--blue)}
.about-photo{left:128px;top:858px;width:440px;height:440px;border-radius:50%;border:8px solid var(--white);box-shadow:0 2px 10px rgba(0,0,0,.2);background:radial-gradient(circle at 40% 40%,#f0ece2,#a8c66a 70%,#6a9a34)}
.h2{font-weight:700;color:var(--ink)}
.about-title{left:640px;top:893px;font-size:36px}
.about-text{left:640px;top:960px;width:448px;font-size:13.5px;line-height:26px;color:#555;text-align:justify}

/* helping orgs */
.orgs{left:0;top:1393px;width:1200px;height:541px;background:var(--soft)}
.orgs-title{left:0;top:1445px;width:1200px;text-align:center;font-size:30px;font-weight:600}
.card-photo{top:1523px;width:314px;height:210px;border-radius:4px}
.card-box{top:1702px;width:290px;height:172px;background:var(--white);border-radius:6px;box-shadow:0 2px 8px rgba(0,0,0,.12);text-align:center;padding:18px 8px 0}
.card-box h3{font-size:15.5px;font-weight:600;color:var(--blue);white-space:nowrap}
.card-box p{font-size:13.5px;line-height:23px;color:#666;margin:12px 10px 0;height:70px}
.more{display:inline-flex;align-items:center;gap:8px;font-size:13px;font-weight:700;color:var(--teal);margin-top:4px}
.more i{width:12px;height:12px;border-radius:50%;background:var(--teal);position:relative}
.more i::after{content:"";position:absolute;left:3px;top:4px;width:3px;height:3px;border-right:1.5px solid var(--white);border-top:1.5px solid var(--white);transform:rotate(45deg)}

/* features */
.frame-teal{left:112px;top:2032px;width:446px;height:340px;border:6px solid var(--teal);border-radius:8px}
.frame-blue{left:642px;top:2493px;width:446px;height:340px;border:6px solid var(--blue);border-radius:8px}
.feat-photo{width:446px;height:340px;border:8px solid var(--white);box-shadow:0 2px 10px rgba(0,0,0,.2)}
.icon-badge{width:80px;height:80px;border-radius:50%;background:var(--white);box-shadow:0 2px 8px rgba(0,0,0,.15);display:flex;align-items:center;justify-content:center}
.icon-badge svg{width:40px;height:40px;fill:none;stroke:var(--teal);stroke-width:2}
.feat-title{font-size:24px;line-height:33px;font-weight:600;color:var(--ink)}
.feat-text{font-size:14px;line-height:26px;color:var(--muted)}

/* book */
.book-bg{left:0;top:3180px;width:1200px;height:413px;background:linear-gradient(180deg,#7c7a4e 0%,#b49960 35%,#8fa04d 65%,#5d7a2f 100%)}
.book-box{left:179px;top:2940px;width:840px;height:314px;background:var(--teal)}
.book-title{left:179px;top:2998px;width:600px;text-align:center;font-size:28px;line-height:34px;font-weight:700;color:var(--white)}
.book-sub{left:179px;top:3078px;width:600px;text-align:center;font-size:16.5px;line-height:27px;font-weight:600;color:var(--white)}
.book-cover{left:772px;top:2962px;width:175px;height:270px;background:linear-gradient(180deg,#f4f1ec 0%,#e9e3dc 55%,#b43a3a 100%);box-shadow:6px 6px 10px rgba(0,0,0,.3)}

/* staying ahead */
.ahead-frame{left:191px;top:3700px;width:818px;height:171px;border:5px solid var(--teal);border-radius:8px}
.ahead-title{left:440px;top:3672px;width:320px;text-align:center;background:var(--white);font-size:37px;font-weight:700;color:var(--ink)}
.ahead-text{left:191px;top:3746px;width:818px;text-align:center;font-family:"Varela Round",sans-serif;font-size:27px;line-height:38px;color:#777}

/* footer */
.footer-wave{left:0;top:3930px;width:1200px;height:498px}
.footer .brand{color:var(--white)}
.footer-menu{left:0;top:4241px;width:1200px;display:flex;justify-content:center;gap:34px;font-size:15px;font-weight:700;color:var(--white)}
.footer-info{left:0;top:4274px;width:1200px;display:flex;justify-content:center;align-items:center;gap:14px;font-size:16px;color:var(--white)}
.footer-info svg{width:14px;height:14px;fill:var(--white);margin-right:8px;vertical-align:-1px}
.copy{left:0;top:4389px;width:1200px;text-align:center;font-size:12px;color:var(--white)}
</style>
</head>
<body>

<!-- top bar -->
<div class="abs topbar"></div>
<div class="abs topbar-blue"></div>
<div class="abs topbar-info">
  <span><svg viewBox="0 0 16 16"><path d="M1 3h14v10H1z M1 3l7 6 7-6" stroke="#0aa39a" stroke-width="1.2"/></svg>info@brightmeadow.studio</span>
  <span>|</span>
  <span><svg viewBox="0 0 16 16"><path d="M8 0a5.5 5.5 0 0 0-5.5 5.5C2.5 10 8 16 8 16s5.5-6 5.5-10.5A5.5 5.5 0 0 0 8 0zm0 8a2.5 2.5 0 1 1 0-5 2.5 2.5 0 0 1 0 5z"/></svg>4870 Meadowlark Ave Springfield IL 62704</span>
</div>
<div class="abs social" style="left:966px;top:6px"></div>
<div class="abs social" style="left:1009px;top:6px"></div>
<div class="abs social" style="left:1052px;top:6px"></div>

<!-- nav -->
<header class="abs nav">
  <div class="abs brand"><span class="brand-dot"></span>Marion Vale Ph.D.</div>
  <nav class="abs menu">
    <span class="caret">THE CENTER</span>
    <span class="caret">HELPING ORGANIZATIONS</span>
    <span class="caret">TEACHING TRAINERS</span>
    <span>RESEARCH</span>
    <span>CONTACT</span>
  </nav>
</header>

<!-- hero -->
<div class="abs hero-photo" role="img" aria-label="Photo of a woman training a white Labrador jumping on green grass in a park"></div>
<h1 class="abs hero-title">THE BRIGHT MEADOW CENTER<br>FOR MEDICAL ASSISTANCE CANINES</h1>
<a class="abs pill teal" style="left:112px;top:407px;width:196px;height:48px">ONLINE COACHING</a>
<a class="abs pill blue" style="left:318px;top:407px;width:196px;height:48px">IN PERSON COACHING</a>
<svg class="abs hero-wave" viewBox="0 0 1200 300" preserveAspectRatio="none">
  <path d="M0,265 C200,110 450,40 700,80 C900,110 1050,95 1200,20 L1200,300 L0,300 Z" fill="#1f6fc3"/>
  <path d="M0,300 C200,120 450,50 700,88 C900,120 1050,110 1200,45 L1200,300 Z" fill="#0aa39a"/>
  <path d="M0,300 C220,140 470,60 700,100 C900,135 1060,145 1200,80 L1200,300 Z" fill="#ffffff"/>
</svg>

<!-- about -->
<div class="abs about-ring"></div>
<div class="abs about-photo" role="img" aria-label="Photo of a woman shaking paws with a beagle"></div>
<h2 class="abs h2 about-title">ABOUT US</h2>
<p class="abs about-text">The Bright Meadow Center for Medical Assistance Canines (BMCA) offers a variety of teaching and coaching services. Marion Vale Ph.D. assists organizations in developing and implementing new service dog programs and teaches professional dog trainers about medical assistance dogs. When the situation allows, she offers in-person tailored consulting services based on the organization’s needs or online options.</p>
<a class="abs pill teal" style="left:640px;top:1207px;width:149px;height:48px">LEARN MORE</a>

<!-- helping organizations -->
<section class="abs orgs"></section>
<h2 class="abs orgs-title">HELPING ORGANIZATIONS</h2>

<div class="abs card-photo" style="left:112px;background:linear-gradient(160deg,#c9ccd6,#5b6e8c 60%,#3a3f4a)" role="img" aria-label="Group photo of trainers with their dogs"></div>
<div class="abs card-box" style="left:124px">
  <h3>PROGRAM CONSULTING</h3>
  <p>Helping organizations get started, improve their training program, and add services</p>
  <a class="more">LEARN MORE <i></i></a>
</div>

<div class="abs card-photo" style="left:442px;background:linear-gradient(160deg,#b9a98e,#6a5a4a 60%,#3a3330)" role="img" aria-label="Audience attending a seminar presentation"></div>
<div class="abs card-box" style="left:454px">
  <h3>PRESENTATIONS &amp; SEMINARS</h3>
  <p>Sharing knowledge about service dogs and medical detection.</p>
  <a class="more">LEARN MORE <i></i></a>
</div>

<div class="abs card-photo" style="left:774px;background:linear-gradient(160deg,#e7edf2,#aeb8bd 60%,#6b5140)" role="img" aria-label="Service dog in a vest looking out an airport window"></div>
<div class="abs card-box" style="left:786px">
  <h3>INTERNATIONAL SERVICES</h3>
  <p>Fluent in both English and French, in-person and online coaching around the world.</p>
  <a class="more">LEARN MORE <i></i></a>
</div>

<!-- coaching -->
<div class="abs frame-teal"></div>
<div class="abs feat-photo" style="left:135px;top:2056px;background:linear-gradient(160deg,#ece9e2,#8b7a66 55%,#3d4a5a)" role="img" aria-label="Trainer working with a black dog indoors"></div>
<div class="abs icon-badge" style="left:644px;top:2062px">
  <svg viewBox="0 0 40 40"><circle cx="14" cy="8" r="3"/><path d="M14 12v14M10 16h8M14 26l-3 9M14 26l3 9M22 34h12l-2-8h-6z M28 26v-4"/></svg>
</div>
<h3 class="abs feat-title" style="left:646px;top:2166px">PROFESSIONAL COACHING/<br>TEACHING FOR DOG TRAINERS</h3>
<p class="abs feat-text" style="left:646px;top:2244px;width:450px">Helping dog trainers improve their skills and learn about service dog training and medical alert dog training.</p>
<a class="abs pill teal" style="left:646px;top:2322px;width:150px;height:49px">LEARN MORE</a>

<!-- research -->
<div class="abs icon-badge" style="left:110px;top:2525px">
  <svg viewBox="0 0 40 40"><circle cx="13" cy="13" r="5"/><circle cx="24" cy="24" r="7"/><path d="M29 29l7 7"/></svg>
</div>
<h3 class="abs feat-title" style="left:112px;top:2626px">COLLABORATING IN RESEARCH<br>PROJECTS</h3>
<p class="abs feat-text" style="left:112px;top:2705px;width:460px">Collaborating in research studies in the field of Medical Detection Dogs.</p>
<a class="abs pill teal" style="left:112px;top:2785px;width:150px;height:48px">LEARN MORE</a>
<div class="abs frame-blue"></div>
<div class="abs feat-photo" style="left:615px;top:2516px;background:linear-gradient(160deg,#e9e5de,#c8bfb2 55%,#9a9a92)" role="img" aria-label="Detection dog sniffing metal cans on a tiled floor"></div>

<!-- book -->
<div class="abs book-bg" role="img" aria-label="Photo of a Labrador leaping for a ball outdoors"></div>
<div class="abs book-box"></div>
<h2 class="abs book-title">NEW BOOK FROM MARION<br>VALE PH.D.!</h2>
<p class="abs book-sub">Choosing And Raising Your Assistance Dog: A Guide<br>to Calm Public Outings</p>
<a class="abs pill white" style="left:404px;top:3155px;width:148px;height:51px">ORDER NOW</a>
<div class="abs book-cover" role="img" aria-label="Book cover of the new assistance dog guide"></div>

<!-- staying ahead -->
<div class="abs ahead-frame"></div>
<h2 class="abs ahead-title">STAYING AHEAD</h2>
<p class="abs ahead-text">Science-based and ethical training methods for the<br>modern service dog trainer</p>
<a class="abs pill teal" style="left:524px;top:3847px;width:150px;height:48px">GET STARTED</a>

<!-- footer -->
<footer class="footer">
  <svg class="abs footer-wave" viewBox="0 0 1200 498" preserveAspectRatio="none">
    <path d="M0,80 C250,20 500,140 760,110 C950,85 1100,40 1200,0 L1200,498 L0,498 Z" fill="#1f6fc3"/>
    <path d="M0,100 C260,40 520,160 780,130 C970,108 1110,70 1200,40 L1200,498 L0,498 Z" fill="#0aa39a"/>
    <path d="M0,120 C260,60 520,180 790,150 C980,128 1110,100 1200,80 L1200,498 L0,498 Z" fill="#2c2c2c"/>
  </svg>
  <div class="abs brand" style="left:472px;top:4170px"><span class="brand-dot" style="border-color:#fff"></span>Marion Vale Ph.D.</div>
  <nav class="abs footer-menu">
    <span>THE CENTER</span><span>HELPING ORGANIZATIONS</span><span>TEACHING TRAINERS</span><span>RESEARCH</span><span>CONTACT</span>
  </nav>
  <div class="abs footer-info">
    <span><svg viewBox="0 0 16 16"><path d="M1 3h14v10H1z"/></svg>info@brightmeadow.studio</span>
    <span>|</span>
    <span><svg viewBox="0 0 16 16"><path d="M8 0a5.5 5.5 0 0 0-5.5 5.5C2.5 10 8 16 8 16s5.5-6 5.5-10.5A5.5 5.5 0 0 0 8 0zm0 8a2.5 2.5 0 1 1 0-5 2.5 2.5 0 0 1 0 5z"/></svg>4870 Meadowlark Ave Springfield IL 62704</span>
  </div>
  <div class="abs social" style="left:539px;top:4315px"></div>
  <div class="abs social" style="left:583px;top:4315px"></div>
  <div class="abs social" style="left:627px;top:4315px"></div>
  <p class="abs copy">© 2021 Company Name. All Rights Reserved</p>
</footer>

</body>
</html>
```